Logistics Website Design

See website https://tqfreightglobal.com for theme and color details. Need the site to be re-done and reflect some of the designs shown in this list here: https://pixelvane.com/tags/logistics-company-website

Target Market(s)

Logistics & Transportation

Industry/Entity Type

Logistics and Supply Chain

Coding

Number of Pages Required

5+ page

Requirements
Must have
• Colors must match theme of logo. Looking for a sleek, interactive design.

```html
<!DOCTYPE html>
<html lang="en">
<head>
<meta charset="utf-8">
<title>TQ Freight Global — Delivering Strength in Every Mile</title>
<link rel="stylesheet" href="https://fonts.googleapis.com/css2?family=Archivo:wght@500;600;700;800&family=Manrope:wght@300;400;500;600&family=Space+Grotesk:wght@500;600;700&display=swap">
<style>
  :root {
    --bg: #1c0f0b;
    --bg-alt: #23140f;
    --card: #2a1912;
    --card-line: #3a261d;
    --accent: #ff8a65;
    --accent-deep: #f47650;
    --cream: #fde4d8;
    --text: #f3e3da;
    --muted: #bfa69a;
    --dim: #8e7569;
  }
  * { box-sizing: border-box; margin: 0; padding: 0; }
  html, body { width: 1200px; height: 2902px; overflow: hidden; }
  body { background: var(--bg); color: var(--text); font-family: "Manrope", sans-serif; position: relative; }
  .abs { position: absolute; }
  .display { font-family: "Archivo", sans-serif; font-weight: 800; text-transform: uppercase; letter-spacing: -0.01em; }
  .eyebrow { font-family: "Space Grotesk", sans-serif; font-weight: 600; text-transform: uppercase; letter-spacing: 0.18em; color: var(--accent); }

  /* Hero */
  .hero { position: absolute; left: 0; top: 0; width: 1200px; height: 787px; overflow: hidden; }
  .hero-photo { position: absolute; inset: 0;
    background:
      radial-gradient(ellipse 520px 300px at 880px 170px, rgba(230,130,80,.55), transparent 70%),
      radial-gradient(ellipse 400px 420px at 920px 420px, rgba(20,12,10,.85), transparent 75%),
      linear-gradient(180deg, #6b3a28 0%, #4a281c 30%, #2e1912 60%, #1f110c 100%); }
  .hero-shade { position: absolute; inset: 0; background: linear-gradient(90deg, rgba(28,15,11,.85) 0%, rgba(28,15,11,.45) 50%, rgba(28,15,11,.1) 100%); }
  .nav { position: absolute; left: 0; top: 0; width: 1200px; height: 113px; background: rgba(28,15,11,.35); border-bottom: 1px solid rgba(255,255,255,.06); }
  .brand { position: absolute; left: 75px; top: 36px; display: flex; align-items: center; gap: 10px; }
  .brand-dot { width: 28px; height: 28px; border-radius: 50%; background: var(--accent); }
  .brand-name { font-family: "Archivo", sans-serif; font-weight: 700; font-size: 20px; color: var(--cream); text-transform: uppercase; }
  .nav-links { position: absolute; left: 431px; top: 46px; display: flex; gap: 30px; font-family: "Archivo", sans-serif; font-weight: 600; font-size: 14px; letter-spacing: -0.02em; text-transform: uppercase; color: var(--text); }
  .nav-links .active { color: var(--accent); border-bottom: 2px solid var(--accent); padding-bottom: 6px; }
  .btn { display: flex; align-items: center; justify-content: center; font-family: "Archivo", sans-serif; font-weight: 700; text-transform: uppercase; letter-spacing: -0.03em; border-radius: 4px; }
  .btn-solid { background: var(--accent); color: #2a120a; }
  .btn-ghost { border: 2px solid rgba(255,255,255,.25); color: var(--cream); background: rgba(28,15,11,.35); }
  .nav-cta { left: 1015px; top: 39px; width: 110px; height: 35px; font-size: 14px; }
  .hero-eyebrow { left: 75px; top: 154px; font-size: 13px; display: flex; align-items: center; gap: 12px; }
  .hero-eyebrow::before { content: ""; width: 7px; height: 7px; border-radius: 50%; background: var(--accent); }
  .hero-title { left: 75px; top: 195px; font-size: 90px; line-height: 90px; color: var(--cream); letter-spacing: -0.005em; }
  .hero-sub { left: 75px; top: 484px; font-size: 20px; color: #fff; }
  .hero-quote { left: 75px; top: 568px; width: 220px; height: 65px; font-size: 18px; box-shadow: 0 10px 30px rgba(255,138,101,.3); }
  .hero-track { left: 310px; top: 568px; width: 220px; height: 65px; font-size: 18px; }
  .stats { position: absolute; left: 583px; top: 575px; width: 617px; height: 212px; background: rgba(28,15,11,.6); }
  .stat { position: absolute; top: 60px; }
  .stat-value { font-family: "Archivo", sans-serif; font-weight: 700; font-size: 36px; color: var(--accent); line-height: 1; }
  .stat-label { font-family: "Space Grotesk", sans-serif; font-weight: 600; font-size: 13px; letter-spacing: .14em; color: var(--text); margin-top: 8px; }

  /* Services */
  .services { position: absolute; left: 0; top: 787px; width: 1200px; height: 656px; background: var(--bg); }
  .section-title { left: 60px; top: 90px; font-size: 43px; color: var(--cream); letter-spacing: -0.03em; }
  .title-rule { left: 60px; top: 150px; width: 90px; height: 3px; background: var(--accent); }
  .card { position: absolute; top: 215px; width: 256px; height: 349px; background: var(--card); border: 1px solid var(--card-line); border-radius: 6px; padding: 30px 24px 0; }
  .card-icon { height: 50px; width: 74px; background: linear-gradient(135deg, #f4a58a, #c96a4d); border-radius: 4px; opacity: .85; }
  .card-title { font-family: "Archivo", sans-serif; font-weight: 700; font-size: 21px; line-height: 30px; text-transform: uppercase; color: var(--cream); margin-top: 24px; letter-spacing: -0.02em; }
  .card-text { font-size: 13px; line-height: 20px; color: var(--muted); font-weight: 300; margin-top: 18px; }
  .card-link { position: absolute; left: 24px; bottom: 30px; font-family: "Space Grotesk", sans-serif; font-weight: 700; font-size: 13px; letter-spacing: .12em; color: var(--accent); }

  /* Supply chain */
  .supply { position: absolute; left: 0; top: 1443px; width: 1200px; height: 662px; background: var(--bg-alt); }
  .supply-photo { left: 60px; top: 90px; width: 509px; height: 481px; border-radius: 6px;
    background: linear-gradient(120deg, #d9b6a6 0%, #a88e8c 35%, #6a5c62 60%, #2a2326 100%); }
  .badge { left: 383px; top: 510px; width: 209px; height: 84px; background: #1e110c; border: 1px solid var(--card-line); border-radius: 6px; display: flex; align-items: center; gap: 16px; padding: 0 22px; }
  .badge-name { font-family: "Archivo", sans-serif; font-weight: 700; font-size: 14px; color: var(--cream); text-transform: uppercase; letter-spacing: -0.03em; }
  .badge-sub { font-size: 11px; color: var(--muted); margin-top: 2px; }
  .supply-title { left: 630px; top: 118px; font-size: 45px; line-height: 55px; color: var(--cream); }
  .supply-title span { color: var(--accent); }
  .supply-text { left: 630px; top: 252px; width: 500px; font-size: 15.5px; line-height: 18px; color: var(--text); font-weight: 400; }
  .checks { left: 630px; top: 388px; list-style: none; }
  .checks li { display: flex; align-items: center; gap: 14px; font-size: 16px; height: 37.5px; color: var(--text); }
  .tick { width: 22px; height: 22px; border-radius: 3px; background: #4a2b1f; display: flex; align-items: center; justify-content: center; }
  .supply-link { left: 630px; top: 526px; font-size: 14px; display: flex; align-items: center; gap: 10px; }

  /* CTA */
  .cta { position: absolute; left: 30px; top: 2105px; width: 1140px; height: 397px; border-radius: 22px; overflow: hidden;
    background: linear-gradient(100deg, #4a342a 0%, #3d2a22 45%, #4d362b 75%, #3a261d 100%); }
  .cta-title { left: 0; width: 1140px; top: 76px; text-align: center; font-size: 56px; color: var(--cream); letter-spacing: -0.04em; }
  .cta-title span { color: var(--accent); }
  .cta-text { left: 0; width: 1140px; top: 165px; text-align: center; font-size: 19.5px; line-height: 27px; color: var(--muted); font-weight: 300; }
  .cta-quote { left: 299px; top: 259px; width: 246px; height: 63px; font-size: 18px; }
  .cta-phone { left: 605px; top: 275px; display: flex; align-items: center; gap: 14px; font-family: "Archivo", sans-serif; font-weight: 700; font-size: 19px; color: var(--cream); letter-spacing: -0.04em; }

  /* Footer */
  .footer { position: absolute; left: 0; top: 2502px; width: 1200px; height: 400px; background: #1a0d09; }
  .footer-brand { left: 45px; top: 78px; display: flex; align-items: center; gap: 8px; }
  .footer-brand .brand-dot { width: 20px; height: 20px; }
  .footer-brand .brand-name { font-size: 15px; }
  .footer-about { left: 45px; top: 155px; width: 245px; font-size: 11.5px; line-height: 17px; color: var(--muted); }
  .col-head { font-family: "Space Grotesk", sans-serif; font-weight: 700; font-size: 11px; letter-spacing: .14em; color: var(--accent); }
  .col { position: absolute; top: 80px; }
  .col ul { list-style: none; margin-top: 33px; }
  .col li { font-size: 13.5px; color: var(--muted); height: 34px; }
  .news-text { font-size: 13.5px; line-height: 20px; color: var(--muted); margin-top: 30px; width: 220px; }
  .news-form { display: flex; gap: 8px; margin-top: 22px; }
  .news-input { width: 195px; height: 41px; border: 1px solid var(--card-line); border-radius: 4px; background: #150a07; font-size: 13px; color: var(--dim); display: flex; align-items: center; padding: 0 12px; }
  .news-send { width: 41px; height: 41px; border-radius: 4px; background: var(--accent); display: flex; align-items: center; justify-content: center; }
  .legal { top: 355px; font-size: 11px; color: var(--dim); text-transform: uppercase; }
</style>
</head>
<body>

<header class="hero">
  <div class="hero-photo" role="img" aria-label="Semi truck with refrigerated trailer on a coastal road at sunset"></div>
  <div class="hero-shade"></div>
  <nav class="nav">
    <div class="brand"><span class="brand-dot"></span><span class="brand-name">TQ Freight Global</span></div>
    <div class="nav-links">
      <span class="active">Home</span><span>Services</span><span>Tracking</span><span>About Us</span>
    </div>
    <a class="abs btn btn-solid nav-cta">Get Quote</a>
  </nav>
  <p class="abs eyebrow hero-eyebrow">Active Logistics Command</p>
  <h1 class="abs display hero-title">Delivering<br>Strength in<br>Every Mile</h1>
  <p class="abs hero-sub">Secure and reliable transportation for all your cargo needs.</p>
  <a class="abs btn btn-solid hero-quote">Request a Quote</a>
  <a class="abs btn btn-ghost hero-track">Track Shipment</a>
  <div class="stats">
    <div class="stat" style="left:58px"><div class="stat-value">2.4M+</div><div class="stat-label">MILES DELIVERED</div></div>
    <div class="stat" style="left:313px"><div class="stat-value">100%</div><div class="stat-label">SAFETY RATING</div></div>
  </div>
</header>

<section class="services">
  <h2 class="abs display section-title">Our Services</h2>
  <div class="abs title-rule"></div>
  <article class="card" style="left:60px">
    <div class="card-icon" role="img" aria-label="Flatbed truck icon" style="width:64px"></div>
    <h3 class="card-title">Flatbed<br>Transportation</h3>
    <p class="card-text">From routine shipments to oversized and heavy-haul loads, we handle freight requiring proper securement, regulatory knowledge, and consistent on-time execution.</p>
    <a class="card-link">LEARN MORE →</a>
  </article>
  <article class="card" style="left:335px">
    <div class="card-icon" role="img" aria-label="Step deck truck icon" style="width:70px"></div>
    <h3 class="card-title" style="margin-top:30px">Step Deck<br>Transportation</h3>
    <p class="card-text">Our step deck trucking services support tall, heavy, and specialized freight that requires additional height clearance and flexible loading options.</p>
    <a class="card-link">LEARN MORE →</a>
  </article>
  <article class="card" style="left:610px">
    <div class="card-icon" role="img" aria-label="Dry van truck icon" style="width:90px"></div>
    <h3 class="card-title" style="margin-top:30px">Dry Van<br>Transportation</h3>
    <p class="card-text">From consumer goods to industrial materials, our dry van services provide the space, security, and consistency you need coast to coast.</p>
    <a class="card-link">LEARN MORE →</a>
  </article>
  <article class="card" style="left:885px">
    <div class="card-icon" role="img" aria-label="Heavy haul tanker truck icon" style="width:88px"></div>
    <h3 class="card-title" style="margin-top:40px">Heavy Haul<br>Transportation</h3>
    <p class="card-text">We provide heavy haul trucking solutions for oversized, overweight, and over-dimensional freight.</p>
    <a class="card-link">LEARN MORE →</a>
  </article>
</section>

<section class="supply">
  <div class="abs supply-photo" role="img" aria-label="Side of a semi truck trailer on a highway at dusk"></div>
  <div class="abs badge">
    <svg width="26" height="26" viewBox="0 0 26 26" fill="none" stroke="#ff8a65" stroke-width="2"><circle cx="13" cy="13" r="10"/><path d="M8.5 13.5l3 3 6-6.5"/></svg>
    <div><div class="badge-name">Elite Carrier</div><div class="badge-sub">DOT Certified &amp; Bonded</div></div>
  </div>
  <h2 class="abs display supply-title">Keeping your supply<br><span>chain moving.</span></h2>
  <p class="abs supply-text">We deliver a comprehensive range of open-deck and specialized transportation services—including flatbed, step deck, heavy haul, and over-dimensional freight solutions. Backed by years of experience, a trusted nationwide carrier network, and a strong safety-first culture, we provide reliable, adaptable logistics support built around the unique requirements of every load.</p>
  <ul class="abs checks">
    <li><span class="tick"><svg width="14" height="14" viewBox="0 0 14 14" fill="none" stroke="#ff8a65" stroke-width="2"><path d="M2.5 7.5l3 3 6-7"/></svg></span>Real-time GPS Tracking on all Assets</li>
    <li><span class="tick"><svg width="14" height="14" viewBox="0 0 14 14" fill="none" stroke="#ff8a65" stroke-width="2"><path d="M2.5 7.5l3 3 6-7"/></svg></span>24/7 Dedicated Logistics Dispatch</li>
    <li><span class="tick"><svg width="14" height="14" viewBox="0 0 14 14" fill="none" stroke="#ff8a65" stroke-width="2"><path d="M2.5 7.5l3 3 6-7"/></svg></span>Custom Rigging &amp; Securement Experts</li>
  </ul>
  <a class="abs eyebrow supply-link">Our Safety Standards
    <svg width="20" height="12" viewBox="0 0 20 12" fill="none" stroke="#ff8a65" stroke-width="2"><path d="M1 6h17M13 1l5 5-5 5"/></svg></a>
</section>

<section class="cta">
  <div class="abs" style="inset:0" role="img" aria-label="Blurred close-up of a trailer in warm light"></div>
  <h2 class="abs display cta-title">Ready to mobilize <span>your cargo?</span></h2>
  <p class="abs cta-text">Get a comprehensive quote within 60 minutes. Our team is standing by to<br>handle your specialized transportation needs.</p>
  <a class="abs btn btn-solid cta-quote">Start Your Quote</a>
  <div class="abs cta-phone">
    <svg width="20" height="20" viewBox="0 0 24 24" fill="none" stroke="#ff8a65" stroke-width="2"><path d="M5 3h4l2 5-2.5 1.5a11 11 0 0 0 6 6L16 13l5 2v4a2 2 0 0 1-2 2A17 17 0 0 1 3 5a2 2 0 0 1 2-2z"/></svg>
    1-800-TQ-FREIGHT
  </div>
</section>

<footer class="footer">
  <div class="abs footer-brand"><span class="brand-dot"></span><span class="brand-name">TQ Freight Global</span></div>
  <p class="abs footer-about">Precision in movement. Power in delivery. The industrial standard for specialized cargo transportation.</p>
  <div class="col" style="left:334px">
    <div class="col-head">SERVICES</div>
    <ul><li>Flatbed Transportation</li><li>Step Deck Freight</li><li>Heavy Haul Logistics</li><li>Dry Van Services</li></ul>
  </div>
  <div class="col" style="left:622px">
    <div class="col-head">COMPANY</div>
    <ul><li>About Us</li><li>Safety &amp; Compliance</li><li>Carrier Network</li><li>Contact Support</li></ul>
  </div>
  <div class="col" style="left:911px">
    <div class="col-head">NEWSLETTER</div>
    <p class="news-text">Stay updated on industry insights and lane updates.</p>
    <div class="news-form">
      <div class="news-input">Email Address</div>
      <div class="news-send"><svg width="18" height="18" viewBox="0 0 24 24" fill="none" stroke="#2a120a" stroke-width="2"><path d="M4 4l17 8-17 8 3-8z"/></svg></div>
    </div>
  </div>
  <p class="abs legal" style="left:45px">© 2026. An independent agent of Halvern Carrier LLC.</p>
  <p class="abs legal" style="left:903px">Privacy Policy</p>
  <p class="abs legal" style="left:1034px">Terms of Service</p>
</footer>

</body>
</html>
```